Quick Straightforward Billboard Redesign

- Design billboard sized for 10 foot' x 36' foot width live area size and please include bleeds 6" around all sides
- Exact blue color match is imperative in headline, logo, phone number bubble or wherever used. C-83 / M-45 / Y-1 / K-0-
- What I hope to illustrate is that our company offers the best porch screening in the area area, in regards to quality, expertise, durability, storms proof, but we do not build screen porches.
- Current board is attached below from previous designer, and as you can see sizing was off, white space on edges make it appear to be sized incorrectly.
- I also attached my own little mock up idea well well if it helps, favorite image, logo, headline, etc and ideas perhaps on expanding or making this better?

Thanks so much!

Target Market(s)

Drivers and passengers, Southeastern NC, are of immense new construction and high end homes.

Industry/Entity Type

Construction

Colors
0054AA
0677BA
7BADD7
CADEEF
E8F1F8

Requirements
Must have
• Blue color matching
Nice to have
• Design spins or other thoughts on my little mock up

```html
<!DOCTYPE html>
<html lang="en">
<head>
<meta charset="utf-8">
<title>Baywater Screens Billboard</title>
<link href="https://fonts.googleapis.com/css2?family=Antonio:wght@600;700&display=swap" rel="stylesheet">
<style>
  :root {
    --brand-blue: #0054AA;
    --brand-green: #1DA84A;
    --board-white: #F4F5F5;
    --stage: #E6E6E6;
  }
  html, body {
    margin: 0;
    width: 1200px;
    height: 900px;
    overflow: hidden;
    background: var(--stage);
  }
  .billboard {
    position: absolute;
    left: 40px;
    top: 294px;
    width: 1120px;
    height: 311px;
    background: var(--board-white);
    overflow: hidden;
    font-family: "Antonio", "Arial Narrow", sans-serif;
  }
  .billboard__art {
    position: absolute;
    inset: 0;
    width: 1120px;
    height: 311px;
  }
  .phone-tab__number {
    position: absolute;
    left: 24px;
    top: 10px;
    margin: 0;
    color: #fff;
    font-weight: 700;
    font-size: 50px;
    line-height: 64px;
    letter-spacing: 0.5px;
    white-space: nowrap;
  }
  .message {
    position: absolute;
    left: 540px;
    top: 0;
    height: 311px;
    display: flex;
    flex-direction: column;
    justify-content: center;
    white-space: nowrap;
  }
  .brand {
    display: flex;
    align-items: center;
    gap: 12px;
    margin: 0 0 10px;
  }
  .brand__mark {
    width: 30px;
    height: 30px;
    background: var(--brand-blue);
  }
  .brand__name {
    color: var(--brand-blue);
    font-weight: 700;
    font-size: 38px;
    line-height: 1;
    text-transform: uppercase;
  }
  .headline {
    margin: 0;
    font-weight: 700;
    font-size: 76px;
    line-height: 1.08;
  }
  .headline__line { display: block; }
  .headline__line--blue { color: var(--brand-blue); }
  .headline__line--green { color: var(--brand-green); }
</style>
</head>
<body>
  <section class="billboard">
    <svg class="billboard__art" viewBox="0 0 1120 311" aria-hidden="true">
      <defs>
        <linearGradient id="porchTones" x1="0" y1="0" x2="0" y2="1">
          <stop offset="0" stop-color="#E9EEF2"/>
          <stop offset="0.35" stop-color="#7BADD7"/>
          <stop offset="0.55" stop-color="#6E9A5A"/>
          <stop offset="1" stop-color="#8A8577"/>
        </linearGradient>
      </defs>
      <polygon points="0,0 472,0 322,311 0,311" fill="url(#porchTones)" role="img" aria-label="Covered screened porch with wicker seating overlooking a lake"/>
      <polygon points="472,0 514,0 364,311 322,311" fill="var(--brand-green)"/>
      <path d="M0 0 H372 C352 0 346 12 336 38 C324 70 306 96 268 96 H0 Z" fill="#fff"/>
      <path d="M0 0 H352 C336 0 330 12 320 34 C310 60 296 86 262 86 H0 Z" fill="var(--brand-blue)"/>
    </svg>

    <p class="phone-tab__number">910.555.0142</p>

    <div class="message">
      <p class="brand">
        <span class="brand__mark"></span>
        <span class="brand__name">Baywater Screens</span>
      </p>
      <h1 class="headline">
        <span class="headline__line headline__line--blue">Screen Your Porch.</span>
        <span class="headline__line headline__line--green">Built for the Coast.</span>
      </h1>
    </div>
  </section>
</body>
</html>
```